Business Card Design

Online clothing womens clothing store, I sell my clothing online and at the markets.

i would like the attached picture on the front of the card and the contact information on the back.

Industry/Entity Type

Business

Contact Information for Business Card

Marlow Thread
Karen Whitfield
(Instagram symbol) _marlow_thread_
(Facebook symbol) www.fakebookexample.com/marlowthreadau/

W : www.marlowthread.example.au
E : info@marlowthread.example.au
P : 0498716204

```html
<!DOCTYPE html>
<html lang="en">
<head>
<meta charset="utf-8">
<title>Marlow Thread – Business Card</title>
<link rel="stylesheet" href="https://fonts.googleapis.com/css2?family=Open+Sans:wght@400;600&display=swap">
<style>
  :root {
    --backdrop: #2b2c2f;
    --card: #1d1d1e;
    --band: #cfd2d3;
    --name-ink: #474849;
    --light-ink: #f1f1f1;
    --photo-light: #dde0e0;
    --photo-mid: #aeb4b8;
    --photo-dark: #4a4d50;
  }
  * { margin: 0; padding: 0; box-sizing: border-box; }
  html, body {
    width: 1200px; height: 864px; overflow: hidden;
    background: var(--backdrop);
    font-family: "Open Sans", sans-serif;
  }
  .stage {
    width: 1200px; height: 864px;
    display: flex; flex-direction: column;
    align-items: center; justify-content: center; gap: 60px;
  }
  .card {
    position: relative;
    width: 560px; height: 320px;
    background: var(--card);
    overflow: hidden;
    box-shadow: 0 6px 18px rgba(0,0,0,.35);
  }

  /* Front */
  .front-band {
    position: absolute; left: 0; right: 0; top: 54px; height: 172px;
    background: linear-gradient(90deg, var(--photo-light) 0%, var(--photo-light) 30%, var(--photo-mid) 52%, var(--photo-dark) 78%, #6e7479 100%);
  }
  .brand-name {
    position: absolute; left: 110px; bottom: 14px;
    color: var(--light-ink);
    font-weight: 600; font-size: 42px; letter-spacing: 2px;
    text-transform: uppercase; white-space: nowrap;
  }

  /* Back */
  .back-band {
    position: absolute; left: 0; right: 0; top: 16px; height: 118px;
    background: var(--band);
    display: flex; align-items: center; justify-content: center;
  }
  .holder-name {
    color: var(--name-ink);
    font-weight: 600; font-size: 22px;
  }
  .contact {
    position: absolute;
    color: var(--light-ink);
    font-size: 13.5px;
    display: flex; align-items: center; gap: 10px;
    white-space: nowrap;
  }
  .contact svg { width: 13px; height: 13px; flex: none; }
  .contact-web { left: 20px; top: 160px; }
  .contact-social { left: 20px; top: 180px; }
  .contact-phone { right: 24px; top: 206px; }
  .contact-mail { right: 24px; top: 228px; }
  .contact-page { left: 150px; top: 254px; }
  .social-mark {
    width: 11px; height: 11px; flex: none;
    background: var(--light-ink); margin: 0 1px;
  }
</style>
</head>
<body>
<main class="stage">

  <section class="card card-front" aria-label="Card front">
    <div class="front-band" role="img" aria-label="Misty grey fashion photograph"></div>
    <h1 class="brand-name">Marlow Thread</h1>
  </section>

  <section class="card card-back" aria-label="Card back">
    <div class="back-band">
      <h2 class="holder-name">Karen Whitfield</h2>
    </div>

    <p class="contact contact-web">
      <svg viewBox="0 0 16 16" fill="none" stroke="currentColor" stroke-width="1.6">
        <rect x="1.5" y="6" width="8" height="4.5" rx="2.2" transform="rotate(-45 5.5 8.2)"/>
        <rect x="6.5" y="5.5" width="8" height="4.5" rx="2.2" transform="rotate(-45 10.5 7.7)"/>
      </svg>
      www.marlowthread.example.au
    </p>
    <p class="contact contact-social">
      <span class="social-mark" aria-hidden="true"></span>
      _marlow_thread_
    </p>
    <p class="contact contact-phone">
      0498716204
      <svg viewBox="0 0 16 16" fill="currentColor">
        <path d="M3.6 1.5l2.2 2.6-1.3 1.6c.9 2 2.4 3.5 4.3 4.4l1.6-1.3 2.6 2.2-1.2 2.3C7.3 14.9 1.1 8.7 1.4 2.7z"/>
      </svg>
    </p>
    <p class="contact contact-mail">
      info@marlowthread.example.au
      <svg viewBox="0 0 16 16" fill="none" stroke="currentColor" stroke-width="1.5">
        <rect x="1.5" y="3.5" width="13" height="9"/>
        <polyline points="1.5,3.5 8,9 14.5,3.5"/>
      </svg>
    </p>
    <p class="contact contact-page">www.fakebookexample.com/marlowthreadau/</p>
  </section>

</main>
</body>
</html>
```